Teach English in China Website Redesign Needed

We recruit native English speakers from the US, UK, etc. who want to teach English as a foreign language in schools in China. Our target customer is college educated, age 22-28 and they love to travel. We prefer designs with bright colors and lots of photos. We want to keep all the text on our current homepage, BrightLanternPost.com. We are open to changing our logo. A competitor's page that we like is pinemeadowtutors.com because of their bright colors, photos and use of white space. We are happy to give you a dofollow link and design credit on our homepage. The use of included photos is optional. We need at least a home page design and a standard blog post design.
Target Market(s)
Our target customer is college educated, age 22-28 and they love to travel. Half of our customers are kindergarten teachers. Half of our customers are male.
Logo Text
Bright Lantern Post
Requirements
Must have
- Bright colors
Should not have
- Our homepage must not look crowded. Use white space effectively.

```html
<!DOCTYPE html>
<html lang="en">
<head>
<meta charset="utf-8">
<title>Bright Lantern Post – Teach In China</title>
<link href="https://fonts.googleapis.com/css2?family=Poppins:wght@400;500;600;700&display=swap" rel="stylesheet">
<style>
:root{
  --red:#e0141c;
  --red-deep:#b80f15;
  --ink:#333333;
  --text:#555555;
  --muted:#8a8a8a;
  --white:#ffffff;
  --soft:#f4f4f4;
}
*{margin:0;padding:0;box-sizing:border-box}
html,body{width:1200px;height:4787px;overflow:hidden;background:var(--white)}
body{font-family:'Poppins',sans-serif;color:var(--text);position:relative}
.abs{position:absolute}
.btn{position:absolute;background:var(--red);color:var(--white);font-weight:600;font-size:17px;display:flex;align-items:center;justify-content:center;border-radius:2px}
.rule{width:70px;height:5px;background:var(--red)}
.section-title{position:absolute;left:0;width:1200px;text-align:center;font-size:56px;font-weight:600;color:var(--ink)}
.center-rule{position:absolute;left:565px}

.hero-photo{position:absolute;left:0;top:0;width:1200px;height:620px;background:linear-gradient(120deg,#5a5550 0%,#8c8379 35%,#b9b0a6 60%,#6e6760 100%)}
.logo{position:absolute;left:232px;top:38px;color:var(--white);font-weight:700;font-size:20px;line-height:23px;width:150px}
.menu{position:absolute;left:574px;top:54px;display:flex;gap:28px;font-size:14px;font-weight:600;color:var(--white)}
.search{position:absolute;left:978px;top:52px}
.hero-title{position:absolute;left:0;top:258px;width:1200px;text-align:center;color:var(--white);font-size:46px;font-weight:600}
.hero-sub{position:absolute;left:0;top:322px;width:1200px;text-align:center;color:var(--white);font-size:15px}
.dots-v{position:absolute;left:1140px;top:258px;display:flex;flex-direction:column;gap:10px}
.dots-v span{width:8px;height:8px;border-radius:50%;background:var(--white);opacity:.7}

.flag-photo{position:absolute;left:0;top:560px;width:660px;height:340px;background:linear-gradient(135deg,var(--red-deep) 0%,var(--red) 55%,#c9151b 100%)}
.flag-text{position:absolute;left:240px;top:605px;color:var(--white);font-size:54px;font-weight:700;line-height:56px}
.intro{position:absolute;left:692px;top:640px;width:330px;font-size:14px;line-height:24px;color:var(--text)}

.highlight-title{position:absolute;left:240px;top:1050px;font-size:58px;font-weight:700;color:var(--ink)}
.hl-item{position:absolute;top:1188px;display:flex;gap:14px;width:230px}
.hl-num{flex:none;width:38px;height:38px;border-radius:50%;background:var(--red);color:var(--white);font-weight:600;display:flex;align-items:center;justify-content:center;font-size:17px}
.hl-item p{font-size:11px;line-height:18px;padding-top:2px}
.dots{position:absolute;display:flex;gap:10px}
.dots span{width:8px;height:8px;border-radius:50%;background:#cfcfcf}
.dots span.on{background:var(--red)}

.body-copy{position:absolute;font-size:14px;line-height:24px;text-align:center}
.blog-img{position:absolute;top:3995px;width:224px;height:145px}
.blog-title{position:absolute;top:4165px;width:224px;font-size:14px;font-weight:600;color:var(--ink);line-height:20px}
.blog-text{position:absolute;top:4232px;width:215px;font-size:10px;line-height:16px}
.footer-bg{position:absolute;left:0;top:4470px;width:1200px;height:317px;background:linear-gradient(180deg,#ffffff 0%,#f3f3f3 55%,#e4e4e4 100%)}
.social{width:20px;height:20px;border-radius:50%;background:var(--ink)}
</style>
</head>
<body>

<!-- Hero -->
<div class="hero-photo" role="img" aria-label="Photo of a smiling teacher in front of a classroom whiteboard with students"></div>
<header>
  <div class="logo">Bright Lantern Post</div>
  <nav class="menu"><span>Home</span><span>Available Jobs</span><span>Apply Online</span><span>Blog</span><span>FAQ</span></nav>
  <svg class="search" width="18" height="18" viewBox="0 0 18 18"><circle cx="7.5" cy="7.5" r="5.5" fill="none" stroke="#e0141c" stroke-width="2.4"/><line x1="11.5" y1="11.5" x2="16" y2="16" stroke="#e0141c" stroke-width="2.4"/></svg>
</header>
<h1 class="hero-title">Teach In China</h1>
<p class="hero-sub">Start an adventure abroad and share the joy of learning English every day</p>
<div class="dots-v"><span></span><span></span><span></span></div>
<div class="btn" style="left:505px;top:380px;width:190px;height:46px">Register Now</div>

<!-- white diagonal under hero -->
<svg class="abs" style="left:0;top:480px" width="1200" height="480" viewBox="0 0 1200 480">
  <polygon points="0,80 1200,20 1200,480 0,480" fill="#ffffff"/>
</svg>

<!-- Intro -->
<div class="flag-photo" role="img" aria-label="Photo of a waving red national flag"></div>
<div class="flag-text">Teach<br>English<br>In China</div>
<div class="rule abs" style="left:240px;top:800px;background:var(--white)"></div>
<div class="intro">Want to teach English in China? Do you enjoy teaching children or adults? Would you like the adventure of teaching in China for a year? Then we have the perfect job for you!<br><br>We are seeking English speakers from the US, UK, Canada, Ireland, Australia, New Zealand and South Africa to teach English in China.</div>
<div class="btn" style="left:692px;top:838px;width:138px;height:46px">Learn More</div>

<!-- Highlight -->
<div class="abs" style="left:0;top:940px;width:1200px;height:470px;background:linear-gradient(180deg,#f7f7f7,#ffffff)"></div>
<section>
  <h2 class="highlight-title">Highlight</h2>
  <div class="rule abs" style="left:240px;top:1140px"></div>
  <div class="dots" style="left:893px;top:1088px"><span class="on"></span><span></span><span></span><span></span></div>
  <div class="hl-item" style="left:246px"><div class="hl-num">1</div><p>Competitive compensation 7000-9000 RMB/month, up to 15000 RMB (Grade 1 to 9) if you have a Bachelor's degree, 2+ years of teaching experience</p></div>
  <div class="hl-item" style="left:496px"><div class="hl-num">2</div><p>Housing allowance 2000 RMB/month (housing is arranged in China)</p></div>
  <div class="hl-item" style="left:734px"><div class="hl-num">3</div><p>Teach private English lessons after work for 200 RMB/hr ($30 US per hour)</p></div>
</section>

<!-- Job Description -->
<h2 class="section-title" style="top:1500px">Job Description</h2>
<div class="rule center-rule" style="top:1600px"></div>
<p class="body-copy" style="left:230px;top:1642px;width:740px">We are seeking English speakers from the US, UK, Canada, Ireland, Australia, New Zealand and South Africa to teach English in China for a year. A Bachelor's degree and experience is recommended, but if you want to work in a kindergarten, you can teach English in China without a degree. If you have a Bachelor's degree, you also have the option to teach older children and adults. Also, more good news is that you do NOT need to know how to speak Chinese.</p>
<div class="btn" style="left:473px;top:1775px;width:254px;height:56px">Current Job Openings</div>

<!-- Apply Now -->
<svg class="abs" style="left:0;top:1900px" width="1200" height="640" viewBox="0 0 1200 640" role="img" aria-label="Photo of a smiling young male teacher in a classroom">
  <defs><linearGradient id="applyPhoto" x1="0" x2="1" y1="0" y2="0"><stop offset="0" stop-color="#e2e0da"/><stop offset=".55" stop-color="#d6d1c9"/><stop offset="1" stop-color="#bdb3a7"/></linearGradient></defs>
  <polygon points="0,40 1200,0 1200,580 0,640" fill="url(#applyPhoto)"/>
</svg>
<h2 class="abs" style="left:245px;top:2010px;font-size:56px;font-weight:600;color:var(--ink)">Apply Now</h2>
<p class="abs" style="left:245px;top:2093px;font-size:16px;color:var(--text)">Fill out our short form and upload your resume</p>
<p class="abs" style="left:235px;top:2200px;width:460px;font-size:13px;line-height:21px;color:var(--muted)">Please make sure you read our FREQUENTLY ASKED QUESTIONS before submitting your information. Interestingly, the FAQ page explains that you must pay your own plane ticket to China. Leaving early, you must assume all conditions at the end of your one year contract. Also, if you are Asian we highly suggest you first watch the video about teachers in China.</p>
<div class="btn" style="left:235px;top:2365px;width:150px;height:46px">Apply Now</div>

<!-- Testimonials -->
<h2 class="section-title" style="top:2595px">Testimonials</h2>
<div class="rule center-rule" style="top:2695px"></div>
<div class="abs" role="img" aria-label="Round portrait photo of a young man" style="left:528px;top:2748px;width:144px;height:144px;border-radius:50%;background:radial-gradient(circle at 50% 40%,#6a6a6a,#1c1c1c)"></div>
<h3 class="abs" style="left:0;top:2915px;width:1200px;text-align:center;color:var(--red);font-size:26px;font-weight:600">Leo Harlan</h3>
<p class="body-copy" style="left:235px;top:2975px;width:730px;font-size:15px;line-height:28px">Marisa was extremely helpful during the entire process. Moving to another country is a very challenging ordeal and having someone like Marisa on your side makes all the difference. She's continued to be incredibly helpful even after arriving, fielding every one of my questions and following up with helpful suggestions. She has been a critical part of the process!</p>
<div class="dots" style="left:568px;top:3158px"><span class="on"></span><span></span><span></span><span></span></div>

<!-- FAQ -->
<div class="abs" style="left:0;top:3240px;width:1200px;height:540px;background:linear-gradient(180deg,#ffffff,#f6f6f6 50%,#ffffff)"></div>
<h2 class="section-title" style="top:3330px">FAQ's</h2>
<div class="rule center-rule" style="top:3430px"></div>
<p class="abs" style="left:0;top:3478px;width:1200px;text-align:center;font-size:17px">Read frequently asked questions about our program.</p>
<div class="btn" style="left:480px;top:3538px;width:240px;height:56px">Ask Questions</div>

<!-- Blog -->
<h2 class="section-title" style="top:3835px">Recent Blog Posts</h2>
<div class="rule center-rule" style="top:3935px"></div>

<div class="blog-img" role="img" aria-label="Photo of performers in red costumes at a Chinese festival" style="left:245px;background:linear-gradient(135deg,#2a1a1a,#b3262b 60%,#e7d6c9)"></div>
<div class="blog-img" role="img" aria-label="Photo of a modern Chinese city skyline at sunset" style="left:488px;background:linear-gradient(180deg,#e3a56a,#6f7a8c 60%,#3b4656)"></div>
<div class="blog-img" role="img" aria-label="Photo of children in a classroom in China" style="left:731px;background:linear-gradient(135deg,#b83128,#d9a48c 55%,#6b4a3c)"></div>

<h4 class="blog-title" style="left:245px">Basic Chinese Greetings</h4>
<h4 class="blog-title" style="left:488px">Owen's ESL Lounge for the Best TEFL TESOL Teach Abroad Jobs</h4>
<h4 class="blog-title" style="left:731px">How China Can Get Enough English Language Teachers</h4>

<p class="blog-text" style="left:245px">Chinese is a pretty difficult language for English speakers to learn compared to Spanish or French. However, if you're going to China, take the time to learn some basics.</p>
<p class="blog-text" style="left:488px">If you've considered teaching English abroad, you've almost certainly visited this website. Known as Owen's ESL Lounge, it is one of the oldest and most popular job boards.</p>
<p class="blog-text" style="left:731px">At more than 1 billion people, China's schools face a huge need for English as a second language. Where will all the English teachers come from over the next years?</p>

<div class="btn" style="left:245px;top:4328px;width:120px;height:38px;font-size:14px">Read More</div>
<div class="btn" style="left:488px;top:4328px;width:120px;height:38px;font-size:14px">Read More</div>
<div class="btn" style="left:731px;top:4328px;width:120px;height:38px;font-size:14px">Read More</div>

<!-- Footer -->
<div class="footer-bg" role="img" aria-label="Faint misty mountain landscape backdrop"></div>
<div class="abs" style="left:245px;top:4530px;width:120px;font-size:17px;font-weight:700;line-height:20px;color:var(--ink)">Bright Lantern Post</div>
<div class="abs" style="left:402px;top:4535px;font-size:11px;line-height:20px;color:var(--ink)"><b style="font-weight:600">Quick Links</b><br><br>Home<br>Available Jobs<br>Apply Online<br>Blog<br>FAQ</div>
<div class="abs" style="left:548px;top:4535px;font-size:11px;line-height:18px;color:var(--ink)"><b style="font-weight:600">Contact Us</b><br><br>Marisa Caldwell, Director<br>418 Orchard Lane Suite 12<br>Maple Grove Texas 77010<br><span style="color:var(--red);font-size:16px;font-weight:600;line-height:30px">555-014-2890</span><br>hello@brightlanternpost.com</div>
<div class="abs" style="left:758px;top:4535px;font-size:11px;font-weight:600;color:var(--ink)">Connect With Us</div>
<div class="abs" style="left:758px;top:4575px;display:flex;gap:8px">
  <span class="social" style="background:var(--red)"></span>
  <span class="social"></span>
  <span class="social"></span>
  <span class="social"></span>
</div>
<p class="abs" style="left:0;top:4752px;width:1200px;text-align:center;font-size:10px;color:var(--ink)">© 2021 Company Name | All Rights Reserved</p>
<div class="abs" style="left:1160px;top:4752px;font-size:10px;color:var(--ink)">1/2</div>

</body>
</html>
```